KHL Flyer Design - Sales Flyer

Using our existing black and red color scheme (logo files attached), we want to create an 8.5 x 16" trifold sales flier template (example attached) for our company. Content/copy is not expected—I only need help with the design/layout. I have shared some images of our operations and people for the flier.
For design themes or other content, you can also look at our website (www.kestrelhaul.com) or the attached PowerPoint presentation.
Target Market(s)
Logistics, trucking, storage
Industry/Entity Type
Logistics, trucking, inventory
Look and feel

```html
<!DOCTYPE html>
<html lang="en">
<head>
<meta charset="utf-8">
<title>KHL Trifold Sales Flyer</title>
<link href="https://fonts.googleapis.com/css2?family=Poppins:wght@400;500;600;700;800&display=swap" rel="stylesheet">
<style>
:root{
  --stage:#8b8b8b;
  --red:#e3232b;
  --red-deep:#c81b22;
  --ink:#231f20;
  --dark:#1f1f1f;
  --paper:#ffffff;
  --fold:#f1f1f1;
  --muted:#3a3a3a;
  --line:#9a9a9a;
}
*{margin:0;padding:0;box-sizing:border-box}
html,body{width:1200px;height:1028px;overflow:hidden}
body{background:var(--stage);font-family:'Poppins',sans-serif;position:relative;color:var(--ink)}
.board-label{position:absolute;color:#fff;font-weight:800;font-size:21px;letter-spacing:.5px;transform:translateX(-50%);line-height:1}
.panel{position:absolute;background:var(--paper);overflow:hidden}
.panel svg.art{position:absolute;left:0;top:0}
.outside{left:60px;top:68px;width:798px;height:425px}
.cover{left:879px;top:68px;width:267px;height:425px}
.inside{left:60px;top:542px;width:798px;height:425px}
.back{left:879px;top:542px;width:267px;height:425px}
.abs{position:absolute}
.brand{position:absolute;color:var(--red);font-weight:800;font-size:36px;line-height:1;letter-spacing:1px;display:flex;align-items:center;gap:6px}
.brand .mark{width:10px;height:10px;background:var(--ink)}
.brand.small{font-size:26px}
.intro p{font-size:7.4px;line-height:1.22;color:var(--ink);border-left:2px solid var(--red);padding-left:6px;margin-bottom:10px;font-weight:500}
.contact{text-align:right;color:#fff;font-size:9.4px;line-height:1.15}
.contact b{font-weight:600;display:block}
.contact span{display:block;margin-bottom:7px}
.tagline{text-align:right;color:#fff;font-weight:800;line-height:1.02;text-transform:uppercase}
.tagline .l1{font-size:16px}
.tagline .l2{font-size:21px}
.tagline .l3{font-size:15px}
.web{position:absolute;color:#fff;font-size:10.5px;letter-spacing:2.2px;display:flex;align-items:center;gap:5px;font-weight:400}
.web svg{width:11px;height:11px}
.diff-title{right:543px;top:108px;text-align:right;font-weight:700;font-size:15.5px;line-height:1.02;color:var(--ink)}
.diff-title::after{content:"";display:block;width:38px;height:1px;background:var(--red);margin:5px 0 0 auto}
.value h4{font-size:6.4px;font-weight:600;color:var(--red);display:flex;align-items:center;gap:3px}
.value h4 i{width:5px;height:6px;background:var(--red);border-radius:1px 1px 3px 3px;display:inline-block}
.value p{font-size:6px;line-height:1.22;color:var(--muted);padding-left:9px}
.kd-title,.svc-title{font-weight:800;font-size:15.5px;line-height:1}
.kd-title{color:var(--ink)}
.svc-title{color:#fff}
.kd-item{display:flex;gap:5px;align-items:flex-start;font-size:5.6px;line-height:1.2;color:var(--muted)}
.kd-item i{flex:none;width:15px;height:15px;border:1px solid var(--red);border-radius:50%}
.svc{color:#fff;text-align:center}
.svc h5{font-size:8.4px;font-weight:600;text-align:left}
.svc p{font-size:5.4px;line-height:1.22;color:#e4e4e4}
.banner-text{color:#fff;font-weight:800;font-size:15px}
.pillar{position:absolute;width:76px;text-align:center}
.pillar .dot{width:34px;height:34px;border-radius:50%;margin:0 auto 4px;display:flex;align-items:center;justify-content:center}
.pillar h5{font-size:7.4px;font-weight:600;color:var(--ink)}
.pillar p{font-size:5.4px;line-height:1.22;color:var(--muted)}
</style>
</head>
<body>

<div class="board-label" style="left:472px;top:38px">OUTSIDE</div>
<div class="board-label" style="left:1013px;top:38px">COVER</div>
<div class="board-label" style="left:472px;top:512px">INSIDE</div>
<div class="board-label" style="left:1013px;top:512px">BACK</div>

<svg width="0" height="0" style="position:absolute">
  <defs>
    <linearGradient id="g-yard" x1="0" y1="0" x2="1" y2="1">
      <stop offset="0" stop-color="#c9c0a8"/><stop offset=".5" stop-color="#9c8a70"/><stop offset="1" stop-color="#6f6252"/>
    </linearGradient>
    <linearGradient id="g-sky" x1="0" y1="0" x2="0" y2="1">
      <stop offset="0" stop-color="#7fb0dc"/><stop offset=".5" stop-color="#c9b69a"/><stop offset="1" stop-color="#8d6e52"/>
    </linearGradient>
    <linearGradient id="g-dirt" x1="0" y1="0" x2="1" y2="1">
      <stop offset="0" stop-color="#b98a63"/><stop offset="1" stop-color="#6d5a4a"/>
    </linearGradient>
    <linearGradient id="g-pipe" x1="0" y1="0" x2="1" y2="1">
      <stop offset="0" stop-color="#a69688"/><stop offset="1" stop-color="#5b4e45"/>
    </linearGradient>
    <linearGradient id="g-fade" x1="0" y1="0" x2="1" y2="0">
      <stop offset="0" stop-color="#f4f4f4"/><stop offset="1" stop-color="#d4d4d4"/>
    </linearGradient>
  </defs>
</svg>

<!-- OUTSIDE SPREAD -->
<section class="panel outside">
  <svg class="art" width="798" height="425" viewBox="0 0 798 425">
    <rect x="266" y="0" width="266" height="425" fill="var(--fold)" opacity=".5"/>
    <polygon role="img" aria-label="Photo: wheel loader with forks on a flatbed trailer under a blue sky" points="0,0 238,0 152,131 0,131" fill="url(#g-sky)"/>
    <polygon points="246,0 270,0 190,112 172,112" fill="var(--ink)"/>
    <polygon role="img" aria-label="Photo: aerial view of loaders moving pipe in a dirt yard" points="0,137 114,137 0,300" fill="url(#g-dirt)"/>
    <line x1="0" y1="416" x2="300" y2="416" stroke="var(--ink)" stroke-width="1"/>
    <polygon role="img" aria-label="Photo: white semi truck hauling pipe on a flatbed" points="318,182 438,182 388,262 268,262" fill="url(#g-yard)"/>
    <polygon role="img" aria-label="Photo: aerial view of a pipe storage yard with trucks and cranes" points="518,82 798,82 798,95 652,308 390,308" fill="url(#g-yard)"/>
    <polygon points="437,0 638,0 626,13 425,13" fill="var(--ink)"/>
    <polygon points="642,0 798,0 798,13 630,13" fill="var(--red)"/>
    <polygon points="798,100 798,140 682,310 656,310" fill="var(--ink)"/>
    <polygon points="798,150 798,425 298,425 378,310 692,310" fill="var(--red)"/>
    <polygon points="798,150 798,425 532,425 532,310 692,310" fill="var(--red-deep)" opacity=".35"/>
    <polyline points="740,205 690,280 660,280" fill="none" stroke="#fff" stroke-width=".6" opacity=".7"/>
    <polyline points="420,320 380,370 360,370" fill="none" stroke="#fff" stroke-width=".6" opacity=".6"/>
    <polygon points="354,393 798,393 798,415 340,415" fill="var(--dark)"/>
  </svg>

  <h2 class="abs diff-title">The KHL<br>Difference</h2>
  <div class="abs value" style="left:124px;top:158px;width:130px"><h4><i></i>Integrity</h4><p>we operate with honesty and transparency, building trust through every interaction. We hold ourselves accountable to our clients, partners, and each other.</p></div>
  <div class="abs value" style="left:92px;top:203px;width:170px"><h4><i></i>Safety</h4><p>safety isn’t just a priority; it’s embedded in everything we do. From planning to delivery, we adhere to strict safety protocols to ensure the protection of people, assets and the environment.</p></div>
  <div class="abs value" style="left:55px;top:247px;width:195px"><h4><i></i>Customer Focus</h4><p>our clients are at the heart of our operations. We customize solutions to fit their unique needs, and our team is always ready to go the extra mile to exceed expectations.</p></div>
  <div class="abs value" style="left:27px;top:284px;width:225px"><h4><i></i>Reliability</h4><p>consistency is key. Our commitment to delivering safe, timely, and accurate logistics solutions means you can depend on us, day in and day out.</p></div>
  <div class="abs value" style="left:27px;top:322px;width:225px"><h4><i></i>Innovation</h4><p>in a fast-paced industry, we stay ahead by embracing technology and innovative solutions. We’re always looking for better, smarter ways to serve our clients.</p></div>

  <div class="brand" style="left:340px;top:36px"><span>KHL</span><span class="mark"></span></div>
  <div class="abs intro" style="left:290px;top:96px;width:185px">
    <p>We understand that every business is unique. Our team will work closely with you to create custom solutions that meet your specific needs and challenges.</p>
    <p>Partner with us for seamless, reliable, and cost-effective logistics solutions tailored to your business needs.</p>
  </div>
  <div class="abs contact" style="right:289px;top:330px"><b>Phone</b><span>(555) 014-2260</span><b>Email</b><span>contactus@kestrelhaul.com</span></div>
  <div class="web" style="left:360px;top:397px"><svg viewBox="0 0 12 12"><circle cx="6" cy="6" r="5" fill="none" stroke="#fff"/><ellipse cx="6" cy="6" rx="2.2" ry="5" fill="none" stroke="#fff"/><line x1="1" y1="6" x2="11" y2="6" stroke="#fff"/></svg>kestrelhaul.com</div>

  <div class="brand" style="left:606px;top:36px"><span>KHL</span><span class="mark"></span></div>
  <div class="abs tagline" style="right:17px;top:308px"><div class="l1">Logistics</div><div class="l2">Redefined</div><div class="l3">Tailored solutions for</div><div class="l3">your business needs</div></div>
  <div class="web" style="left:628px;top:397px"><svg viewBox="0 0 12 12"><circle cx="6" cy="6" r="5" fill="none" stroke="#fff"/><ellipse cx="6" cy="6" rx="2.2" ry="5" fill="none" stroke="#fff"/><line x1="1" y1="6" x2="11" y2="6" stroke="#fff"/></svg>kestrelhaul.com</div>
</section>

<!-- COVER -->
<section class="panel cover">
  <svg class="art" width="267" height="425" viewBox="0 0 267 425">
    <polygon role="img" aria-label="Photo: aerial view of a pipe storage yard with trucks and cranes" points="0,82 267,82 267,95 120,308 0,308" fill="url(#g-yard)"/>
    <polygon points="0,0 106,0 94,13 0,13" fill="var(--ink)"/>
    <polygon points="110,0 267,0 267,13 98,13" fill="var(--red)"/>
    <polygon points="267,100 267,140 150,310 124,310" fill="var(--ink)"/>
    <polygon points="267,150 267,425 0,425 0,310 160,310" fill="var(--red)"/>
    <polyline points="208,205 158,280 128,280" fill="none" stroke="#fff" stroke-width=".6" opacity=".7"/>
    <rect x="0" y="393" width="267" height="22" fill="var(--dark)"/>
  </svg>
  <div class="brand" style="left:74px;top:36px"><span>KHL</span><span class="mark"></span></div>
  <div class="abs tagline" style="right:17px;top:310px"><div class="l1">Logistics</div><div class="l2">Redefined</div><div class="l3">Tailored solutions for</div><div class="l3">your business needs</div></div>
  <div class="web" style="left:96px;top:397px"><svg viewBox="0 0 12 12"><circle cx="6" cy="6" r="5" fill="none" stroke="#fff"/><ellipse cx="6" cy="6" rx="2.2" ry="5" fill="none" stroke="#fff"/><line x1="1" y1="6" x2="11" y2="6" stroke="#fff"/></svg>kestrelhaul.com</div>
</section>

<!-- INSIDE SPREAD -->
<section class="panel inside">
  <svg class="art" width="798" height="425" viewBox="0 0 798 425">
    <polygon role="img" aria-label="Photo: crew member in hard hat handling stacked pipe" points="0,0 202,0 334,183 0,183" fill="url(#g-pipe)"/>
    <polygon points="0,70 95,183 0,183" fill="var(--red)"/>
    <polygon points="0,40 20,40 0,62" fill="var(--red)" opacity=".9"/>
    <polygon points="0,190 178,190 198,217 0,217" fill="var(--red)"/>
    <line x1="100" y1="232" x2="100" y2="332" stroke="var(--line)" stroke-dasharray="1.5 1.5" stroke-width=".6"/>
    <line x1="188" y1="232" x2="188" y2="332" stroke="var(--line)" stroke-dasharray="1.5 1.5" stroke-width=".6"/>
    <line x1="0" y1="413" x2="340" y2="413" stroke="var(--ink)" stroke-width="1"/>
    <polygon role="img" aria-label="Faded photo: worker inspecting pipe in the yard" points="266,182 346,182 460,393 266,393" fill="url(#g-fade)"/>
    <polygon points="451,0 798,0 798,393 720,393 545,116" fill="var(--dark)"/>
    <polygon points="465,20 500,20 520,43 485,43" fill="var(--red)"/>
    <polygon points="505,20 530,20 550,43 525,43" fill="var(--red)"/>
    <polygon role="img" aria-label="Photo: close view of pipe ends being checked" points="294,116 410,116 454,179 338,179" fill="url(#g-pipe)"/>
    <polygon role="img" aria-label="Photo: pipe racks outside a storage building" points="413,116 528,116 570,179 456,179" fill="url(#g-yard)"/>
    <polygon role="img" aria-label="Photo: yellow loader moving pipe beside railcars" points="346,182 590,182 714,376 446,376" fill="url(#g-dirt)"/>
    <polygon role="img" aria-label="Photo: truck with crane at a yard" points="512,49 583,49 568,95 497,95" fill="url(#g-yard)"/>
    <polygon role="img" aria-label="Photo: pipe stored on racks" points="546,101 630,101 615,144 531,144" fill="url(#g-pipe)"/>
    <polygon role="img" aria-label="Photo: pipe being transloaded" points="581,153 673,153 658,196 566,196" fill="url(#g-yard)"/>
    <polygon role="img" aria-label="Photo: inspector examining pipe" points="618,205 693,205 678,248 603,248" fill="url(#g-pipe)"/>
    <polygon points="640,258 665,258 798,370 798,393" fill="var(--red)"/>
    <polyline points="680,268 760,340 798,340" fill="none" stroke="var(--red)" stroke-width=".7"/>
    <polygon points="362,393 752,393 774,425 340,425" fill="var(--dark)"/>
    <polygon points="752,393 798,393 798,425 774,425" fill="var(--paper)"/>
  </svg>

  <div class="abs banner-text" style="left:24px;top:194px">VISION &amp; PURPOSE</div>
  <div class="pillar" style="left:18px;top:232px">
    <div class="dot" style="background:var(--red)"><svg width="16" height="16" viewBox="0 0 16 16"><path d="M3 13l3-6 6-4-3 7z" fill="#fff"/></svg></div>
    <h5>VISION</h5><p>To be the leading provider of innovative and reliable logistics solutions, recognized for unwavering dedication to safety, reliability, and superior customer service.</p>
  </div>
  <div class="pillar" style="left:104px;top:232px">
    <div class="dot" style="background:var(--ink)"><svg width="16" height="16" viewBox="0 0 16 16"><circle cx="8" cy="7" r="4" fill="none" stroke="#fff" stroke-width="1.3"/><rect x="6" y="11.5" width="4" height="2" fill="#fff"/></svg></div>
    <h5>INNOVATION</h5><p>We leverage cutting edge technologies to streamline supply chains and maximize value while keeping it simple – getting your product to the right place at the right time.</p>
  </div>
  <div class="pillar" style="left:186px;top:232px">
    <div class="dot" style="background:var(--red)"><svg width="16" height="16" viewBox="0 0 16 16"><circle cx="6" cy="4" r="2" fill="#fff"/><rect x="4" y="7" width="4" height="6" rx="1" fill="#fff"/><circle cx="12" cy="6" r="1.6" fill="none" stroke="#fff"/></svg></div>
    <h5>PEOPLE</h5><p>We are passionate about every job we undertake. You can count on our team to complete each task with integrity, dedication, and enthusiasm.</p>
  </div>

  <div class="abs kd-title" style="left:268px;top:23px">KEY DIFFERENTIATORS</div>
  <div class="abs kd-item" style="left:280px;top:52px;width:100px"><i></i><span>Deep industry knowledge and expertise</span></div>
  <div class="abs kd-item" style="left:390px;top:50px;width:100px"><i></i><span>Monthly cycle counts and spot checks</span></div>
  <div class="abs kd-item" style="left:288px;top:76px;width:94px"><i></i><span>High volume operation with sustained delivery and inventory accuracy performance &gt;99%</span></div>
  <div class="abs kd-item" style="left:390px;top:76px;width:100px"><i></i><span>Quarterly business reviews (QBRs) and monthly inventory reporting</span></div>

  <div class="abs svc-title" style="left:553px;top:23px">SERVICES</div>
  <div class="abs svc" style="left:590px;top:52px;width:170px"><h5>Transportation &amp; Forklift/Crane Rentals</h5><p>From forklifts to trucking, transloading to inspection, we have top-quality options that support you at each step of the process.</p></div>
  <div class="abs svc" style="left:624px;top:103px;width:160px"><h5>Storage</h5><p>Our customized storage solutions let you expand your market reach and strategically position inventory for lower freight costs and efficient distribution.</p></div>
  <div class="abs svc" style="left:660px;top:155px;width:125px"><h5>Transloading</h5><p>Our comprehensive logistics services cover every aspect of rail transportation, from the point of origin to the final destination.</p></div>
  <div class="abs svc" style="left:697px;top:207px;width:90px"><h5>Inspection</h5><p>Trust us to ensure the reliability and safety of your OCTG material. We ensure your product is free from defects by performing both visual and non-destructive testing (NDT).</p></div>

  <div class="brand small" style="left:340px;top:344px"><span>KHL</span><span class="mark" style="width:8px;height:8px"></span></div>
  <div class="web" style="left:366px;top:402px"><svg viewBox="0 0 12 12"><circle cx="6" cy="6" r="5" fill="none" stroke="#fff"/><ellipse cx="6" cy="6" rx="2.2" ry="5" fill="none" stroke="#fff"/><line x1="1" y1="6" x2="11" y2="6" stroke="#fff"/></svg>kestrelhaul.com</div>
  <div class="web" style="left:574px;top:402px"><svg viewBox="0 0 12 12"><circle cx="6" cy="6" r="5" fill="none" stroke="#fff"/><ellipse cx="6" cy="6" rx="2.2" ry="5" fill="none" stroke="#fff"/><line x1="1" y1="6" x2="11" y2="6" stroke="#fff"/></svg>kestrelhaul.com</div>
</section>

<!-- BACK -->
<section class="panel back">
  <svg class="art" width="267" height="425" viewBox="0 0 267 425">
    <polygon points="172,0 267,0 267,12 162,12" fill="var(--ink)"/>
    <polygon role="img" aria-label="Photo: aerial view of a pipe storage yard" points="250,83 267,83 267,309 94,309" fill="url(#g-yard)"/>
    <polygon role="img" aria-label="Photo: white semi truck hauling pipe on a flatbed" points="68,185 172,185 120,263 13,263" fill="url(#g-yard)"/>
    <polygon points="267,310 267,425 30,425 110,312" fill="var(--red)"/>
    <polyline points="140,320 100,372 80,372" fill="none" stroke="#fff" stroke-width=".6" opacity=".6"/>
    <polygon points="100,393 267,393 267,415 86,415" fill="var(--dark)"/>
  </svg>
  <div class="brand" style="left:74px;top:36px"><span>KHL</span><span class="mark"></span></div>
  <div class="abs intro" style="left:22px;top:97px;width:190px">
    <p>We understand that every business is unique. Our team will work closely with you to create custom solutions that meet your specific needs and challenges.</p>
    <p>Partner with us for seamless, reliable, and cost-effective logistics solutions tailored to your business needs.</p>
  </div>
  <div class="abs contact" style="right:23px;top:333px"><b>Phone</b><span>(555) 014-2260</span><b>Email</b><span>contactus@kestrelhaul.com</span></div>
  <div class="web" style="left:95px;top:397px"><svg viewBox="0 0 12 12"><circle cx="6" cy="6" r="5" fill="none" stroke="#fff"/><ellipse cx="6" cy="6" rx="2.2" ry="5" fill="none" stroke="#fff"/><line x1="1" y1="6" x2="11" y2="6" stroke="#fff"/></svg>kestrelhaul.com</div>
</section>

</body>
</html>
```